Business card alterations

I have changed my business name from Brisa Laser Renewal Clinic to simply "Brisa Laser Clinic' and need this logo changed to reflect same

Brisa Laser Clinic
Est. 2004

I also need new business cards with above logo included and this attached card changed to the following.
Marianne Holcroft
Dermal Aesthetician
Grad Cert in Laser & IPL Treatments

I need at least one logo in less than 4mb so I can upload into my newsletter format so I can upload to newsletters, emails etc

Thanks
Mari

```html
<!DOCTYPE html>
<html lang="en">
<head>
<meta charset="utf-8">
<title>Brisa Laser Clinic – Business Card</title>
<link href="https://fonts.googleapis.com/css2?family=Titillium+Web:wght@300;400;600;700&display=swap" rel="stylesheet">
<style>
  :root {
    --page-bg: #ececec;
    --card-green: #05a05f;
    --card-ink: #ffffff;
    --card-shadow: rgba(0, 0, 0, 0.18);
  }
  * { box-sizing: border-box; margin: 0; padding: 0; }
  html, body {
    width: 1200px;
    height: 864px;
    overflow: hidden;
    background: var(--page-bg);
    font-family: "Titillium Web", Arial, sans-serif;
  }
  .business-card {
    position: absolute;
    left: 100px;
    top: 147px;
    width: 1000px;
    height: 570px;
    background: var(--card-green);
    color: var(--card-ink);
    box-shadow: 0 14px 40px var(--card-shadow);
  }
  .brand-block {
    position: absolute;
    left: 70px;
    top: 120px;
    width: 430px;
  }
  .brand-wordmark {
    display: flex;
    align-items: center;
    gap: 18px;
    font-weight: 600;
    font-size: 138px;
    line-height: 1;
    letter-spacing: -2px;
  }
  .brand-dot {
    width: 22px;
    height: 22px;
    border-radius: 50%;
    background: var(--card-ink);
    margin-top: 20px;
  }
  .brand-name {
    margin-top: 22px;
    font-weight: 600;
    font-size: 29px;
    letter-spacing: 7px;
    text-transform: uppercase;
    text-align: right;
    line-height: 1.15;
  }
  .brand-established {
    font-weight: 600;
    font-size: 29px;
    letter-spacing: 7px;
    text-transform: uppercase;
    text-align: center;
    line-height: 1.15;
    padding-left: 60px;
  }
  .qualification {
    margin-top: 12px;
    font-weight: 300;
    font-size: 28px;
    white-space: nowrap;
  }
  .card-divider {
    position: absolute;
    left: 505px;
    top: 90px;
    width: 4px;
    height: 400px;
    background: var(--card-ink);
  }
  .person {
    position: absolute;
    left: 570px;
    top: 95px;
  }
  .person-name {
    font-weight: 700;
    font-size: 32px;
    line-height: 1.1;
  }
  .person-role {
    font-weight: 400;
    font-size: 25px;
    line-height: 1.2;
  }
  .contact-list {
    position: absolute;
    left: 560px;
    top: 305px;
    list-style: none;
  }
  .contact-item {
    display: flex;
    align-items: flex-start;
    gap: 20px;
    font-weight: 400;
    font-size: 24px;
    line-height: 1.3;
    margin-bottom: 9px;
  }
  .contact-icon {
    flex: 0 0 26px;
    width: 26px;
    height: 26px;
    margin-top: 3px;
    fill: var(--card-ink);
    stroke: var(--card-ink);
  }
</style>
</head>
<body>
  <section class="business-card">
    <div class="brand-block">
      <div class="brand-wordmark">Brisa<span class="brand-dot"></span></div>
      <div class="brand-name">Brisa Laser Clinic</div>
      <div class="brand-established">Est. 2004</div>
      <div class="qualification">Grad Cert in Laser &amp; IPL Treatments</div>
    </div>

    <div class="card-divider"></div>

    <div class="person">
      <div class="person-name">Marianne Holcroft</div>
      <div class="person-role">Dermal Aesthetician</div>
    </div>

    <ul class="contact-list">
      <li class="contact-item">
        <svg class="contact-icon" viewBox="0 0 26 26" aria-hidden="true">
          <path stroke="none" d="M3 9c0-3 4-5 10-5s10 2 10 5v2h-5V8.5c-1.5-.7-3-1-5-1s-3.5.3-5 1V11H3z"/>
          <rect stroke="none" x="5" y="12" width="16" height="10" rx="2"/>
        </svg>
        <span>(08) 7100 4821</span>
      </li>
      <li class="contact-item">
        <svg class="contact-icon" viewBox="0 0 26 26" aria-hidden="true">
          <rect x="3" y="6" width="20" height="14" fill="none" stroke-width="2.4"/>
          <path d="M3 6l10 8 10-8M3 20l7-6M23 20l-7-6" fill="none" stroke-width="2"/>
        </svg>
        <span>info@brisaclinic.com.au</span>
      </li>
      <li class="contact-item">
        <svg class="contact-icon" viewBox="0 0 26 26" aria-hidden="true">
          <rect x="3" y="4" width="20" height="14" fill="none" stroke-width="2.4"/>
          <rect stroke="none" x="11" y="18" width="4" height="3"/>
          <rect stroke="none" x="7" y="21" width="12" height="2.4"/>
        </svg>
        <span>www.brisaclinic.com.au</span>
      </li>
      <li class="contact-item">
        <svg class="contact-icon" viewBox="0 0 26 26" aria-hidden="true">
          <path stroke="none" d="M13 3L1 13h3.5L13 6l8.5 7H25z"/>
          <path stroke="none" d="M6 14l7-6 7 6v9h-5v-6h-4v6H6z"/>
        </svg>
        <span>214 Kestrel Road<br>Fernvale SA 5072</span>
      </li>
    </ul>
  </section>
</body>
</html>
```